first fantastic look and impression

We are looking for a concept for letterhead, business card, emailfooter and template for invoices or offers for our company in the consultation business.
The dancer is a symbol who we are: it looks simple, but there is a lot of hard work and many years of training in this movement. The look is also what we want: elegant, modern, strong, with a touch of extravaganza
Target Market(s)
Hotelbusiness , Consulting
Font styles to use
Sans Serif
Other font styles liked:
- please give us a option we are open
Requirements
Must have
- We are not typical consultants but sparring partners and coaches for the hotel and that should also be expressed in the design. Maybe there is an icon that supports the whole thing. We are more modern and bolder than our industry colleagues.
we are modern, fresh, agile, fast
Nice to have
- a icon

```html
<!DOCTYPE html>
<html lang="en">
<head>
<meta charset="utf-8">
<title>Velora – Business Card</title>
<link rel="stylesheet" href="https://fonts.googleapis.com/css2?family=Khand:wght@600&family=Roboto:wght@400&display=swap">
<style>
  :root {
    --backdrop: #6b6b6b;
    --card-dark: #171717;
    --ink: #111111;
    --ink-soft: #2a2a2a;
    --art-high: #4a4a4a;
    --art-mid: #2c2c2c;
    --art-low: #1f1f1f;
  }
  * { margin: 0; padding: 0; box-sizing: border-box; }
  html, body {
    width: 1200px;
    height: 1138px;
    overflow: hidden;
    background: var(--backdrop);
  }
  .canvas {
    position: relative;
    width: 1200px;
    height: 1138px;
  }
  .card {
    position: absolute;
    width: 620px;
    height: 374px;
    border-radius: 14px;
    overflow: hidden;
  }
  .card-front {
    left: 274px;
    top: 186px;
    background: var(--card-dark);
  }
  .dancer-art {
    position: absolute;
    left: 162px;
    top: 56px;
    width: 302px;
    height: 282px;
    border-radius: 18px;
    background:
      radial-gradient(ellipse 60% 45% at 62% 30%, var(--art-high) 0%, transparent 70%),
      radial-gradient(ellipse 55% 60% at 35% 60%, var(--art-mid) 0%, transparent 75%),
      linear-gradient(160deg, var(--art-mid) 0%, var(--art-low) 100%);
    box-shadow: inset 0 0 0 1px rgba(255,255,255,0.06);
  }
  .card-back {
    left: 276px;
    top: 608px;
    background: linear-gradient(180deg, #f4f4f4 0%, #e9e9e9 100%);
    color: var(--ink);
    font-family: "Roboto", sans-serif;
  }
  .brand-name {
    position: absolute;
    left: 78px;
    top: 156px;
    width: 200px;
    text-align: center;
    font-family: "Roboto", sans-serif;
    font-weight: 400;
    font-size: 46px;
    letter-spacing: 1px;
    color: var(--ink);
  }
  .person {
    position: absolute;
    left: 361px;
    top: 84px;
  }
  .person-name {
    font-family: "Khand", sans-serif;
    font-weight: 600;
    font-size: 27px;
    line-height: 1;
  }
  .person-role {
    margin-top: 3px;
    font-size: 17px;
    color: var(--ink-soft);
  }
  .contact-list {
    position: absolute;
    left: 364px;
    top: 164px;
    list-style: none;
  }
  .contact-item {
    display: flex;
    align-items: center;
    height: 24px;
    font-size: 16.5px;
  }
  .contact-icon {
    width: 16px;
    height: 14px;
    margin-right: 13px;
    fill: var(--ink);
  }
  .address {
    position: absolute;
    left: 364px;
    top: 241px;
    font-size: 16.6px;
    line-height: 24px;
    font-style: normal;
  }
</style>
</head>
<body>
<main class="canvas">
  <section class="card card-front">
    <div class="dancer-art" role="img" aria-label="Embossed line illustration of a leaping dancer holding a flowing veil, glossy black on matte black"></div>
  </section>

  <section class="card card-back">
    <div class="brand-name">Velora</div>

    <div class="person">
      <div class="person-name">John Doe Smith</div>
      <div class="person-role">Managing Director</div>
    </div>

    <ul class="contact-list">
      <li class="contact-item">
        <svg class="contact-icon" viewBox="0 0 16 14" aria-hidden="true">
          <path d="M1 4 C1 1.5 15 1.5 15 4 L15 5.5 L11.5 5.5 L11.5 4 L4.5 4 L4.5 5.5 L1 5.5 Z"/>
          <path d="M4 6 L12 6 L14 13 L2 13 Z"/>
        </svg>
        828-111-1111
      </li>
      <li class="contact-item">
        <svg class="contact-icon" viewBox="0 0 16 14" aria-hidden="true">
          <path d="M1 2 L15 2 L8 8 Z"/>
          <path d="M1 3.5 L8 9.5 L15 3.5 L15 12 L1 12 Z"/>
        </svg>
        john@yourwebsite.com
      </li>
      <li class="contact-item">
        <svg class="contact-icon" viewBox="0 0 16 16" aria-hidden="true">
          <circle cx="8" cy="8" r="6.5" fill="none" stroke="#111" stroke-width="1.4"/>
          <ellipse cx="8" cy="8" rx="2.8" ry="6.5" fill="none" stroke="#111" stroke-width="1.2"/>
          <path d="M1.5 8 H14.5 M2.5 5 H13.5 M2.5 11 H13.5" stroke="#111" stroke-width="1.1"/>
        </svg>
        www.yourwebsite.com
      </li>
    </ul>

    <address class="address">
      234 Anywhere St., Any City,<br>
      Any Town, US 123456
    </address>
  </section>
</main>
</body>
</html>
```